Vitamin B12 Liquid Drops Label

hi, i need a label designed for my vitamin b12 drops that i am going to be selling on shopzello. the label needs to quickly capture the attention of a buyer as he or she is scrolling through the thumbnail search results on shopzello.com my brand is called nralo. i already have an example brand logo i will be using, however, i need help designing the rest of the label. attached are some examples of labels i like for other supplements.some of these examples are pink. i do not want pink. please go for a blue/green color scheme. THE DESIGN MUST BE BOLD

Target Market(s)

adults ages 30 - 64

Font styles to use
Sans Serif

Colors
0455a3
cedeed
3176b5
85acd3
cfdeed
9bcb3b
abd037
cadf82
00a990

Requirements
Must have
• - bold design
• - somewhat gender-neutral color scheme because this will be used equally by men and women
• - B12 MUST be very prominent and visible on the label
Should not have
• - it should not be "crunchy" looking

```html
<!DOCTYPE html>
<html lang="en">
<head>
<meta charset="utf-8">
<title>NRALO Supplements – Vitamin B12 Label</title>
<link rel="stylesheet" href="https://fonts.googleapis.com/css2?family=Open+Sans:wdth,wght@75..100,600..800&display=swap">
<style>
  :root {
    --backdrop: #cedeed;
    --panel-green: #9bcb3b;
    --panel-blue: #0455a3;
    --panel-teal: #00a990;
    --brand-blue: #0455a3;
    --accent-green: #cadf82;
  }
  * { margin: 0; padding: 0; box-sizing: border-box; }
  html, body {
    width: 1200px;
    height: 960px;
    overflow: hidden;
    background: var(--backdrop);
  }
  .canvas {
    position: relative;
    width: 1200px;
    height: 960px;
    background: var(--backdrop);
  }
  .label {
    position: absolute;
    left: 196px;
    top: 65px;
    width: 807px;
    height: 830px;
    overflow: hidden;
    font-family: "Open Sans", Arial, sans-serif;
  }
  .label-bg {
    position: absolute;
    inset: 0;
    width: 100%;
    height: 100%;
  }
  .brand-name {
    position: absolute;
    left: 30px;
    top: 262px;
    font-size: 200px;
    font-weight: 800;
    font-stretch: 82%;
    line-height: 1;
    letter-spacing: -2px;
    color: var(--brand-blue);
  }
  .brand-tagline {
    position: absolute;
    left: 52px;
    top: 472px;
    font-size: 36px;
    font-weight: 700;
    letter-spacing: 23px;
    line-height: 1;
    color: var(--accent-green);
  }
  .product-name {
    position: absolute;
    right: 40px;
    top: 700px;
    font-size: 88px;
    font-weight: 800;
    font-stretch: 80%;
    line-height: 1;
    white-space: nowrap;
    color: var(--accent-green);
  }
</style>
</head>
<body>
  <main class="canvas">
    <section class="label">
      <svg class="label-bg" viewBox="0 0 807 830" preserveAspectRatio="none" aria-hidden="true">
        <rect class="panel-blue" x="0" y="0" width="807" height="830" fill="var(--panel-blue)"/>
        <polygon class="panel-teal" points="805,0 807,0 807,40 646,438 630,438" fill="var(--panel-teal)"/>
        <polygon class="panel-green" points="0,0 805,0 630,438 0,438" fill="var(--panel-green)"/>
      </svg>
      <h1 class="brand-name">NRALO</h1>
      <p class="brand-tagline">SUPPLEMENTS</p>
      <h2 class="product-name">VITAMIN B12</h2>
    </section>
  </main>
</body>
</html>
```